Design a poster that illustrates the six central pillars of our school district's efforts with students. The attached PDF outlines the six main competencies we aim for students to possess upon graduation. Each of the 6 has 3 bullet points for the poster as well. The title is "Profile of a Trailblazer". Our mascot is this attached winged wheel. The overall concept is that staff take kids when they are young and develop these 6 things when they graduate. Our colors are navy, red, and white. We will make this poster in a variety of sizes in offices, classrooms, and in digital spaces as well. On the PDF - ignore the column that says "Synthesis". That has nothing to do with this poster.

The district is Harlow Creek Public Schools https://www.harlowcreek-schools.example/

```html
<!DOCTYPE html>
<html lang="en">
<head>
<meta charset="utf-8">
<title>Profile of a Trailblazer — Harlow Creek Public Schools</title>
<link href="https://fonts.googleapis.com/css2?family=Anton&family=Oswald:wght@500;600&family=Montserrat:wght@500&display=swap" rel="stylesheet">
<style>
  :root {
    --navy: #212f48;
    --red: #a51c24;
    --white: #ffffff;
    --backdrop: #e6e6e6;
    --ink: #1e2230;
  }
  * { box-sizing: border-box; margin: 0; padding: 0; }
  html, body { width: 1200px; height: 1200px; overflow: hidden; }
  body { background: var(--backdrop); position: relative; }

  .poster {
    position: absolute; left: 175px; top: 0;
    width: 849px; height: 1200px;
    background: var(--white); overflow: hidden;
  }
  .navy-column {
    position: absolute; left: 0; top: 0;
    width: 411px; height: 1007px; background: var(--navy);
  }

  .title-part {
    position: absolute; top: 50px;
    font-family: "Anton", sans-serif; font-size: 78px; line-height: 1;
    color: var(--red); text-transform: uppercase; letter-spacing: -1px;
    -webkit-text-stroke: 2px var(--white); paint-order: stroke fill;
    text-shadow: 2px 3px 4px rgba(0,0,0,.35);
    white-space: nowrap;
  }
  .title-left { left: 32px; }
  .title-right { left: 425px; font-size: 70px; top: 56px; }

  .pillar { position: absolute; width: 370px; }
  .pillar-left { left: 34px; }
  .pillar-right { left: 427px; width: 400px; }
  .pillar h2 {
    font-family: "Oswald", sans-serif; font-weight: 600;
    font-size: 46px; line-height: 1; letter-spacing: -0.5px;
    margin-bottom: 26px;
  }
  .pillar-left h2 { color: var(--white); }
  .pillar-right h2 { color: var(--red); }

  .traits { list-style: none; position: relative; }
  .traits::before {
    content: ""; position: absolute; left: 6px; top: 6px; bottom: -4px;
    width: 1px;
  }
  .pillar-left .traits::before { background: var(--white); }
  .pillar-right .traits::before { background: var(--navy); }
  .traits li {
    position: relative; padding-left: 32px; margin-bottom: 19px;
    font-family: "Montserrat", sans-serif; font-weight: 500;
    font-size: 15.6px; line-height: 19.4px;
  }
  .traits li:last-child { margin-bottom: 0; }
  .pillar-left .traits li { color: var(--white); }
  .pillar-right .traits li { color: var(--ink); }
  .traits li::before {
    content: ""; position: absolute; left: 0; top: 3px;
    width: 13px; height: 13px;
  }
  .pillar-left .traits li::before { border: 1px solid var(--white); background: var(--navy); }
  .pillar-right .traits li::before { background: var(--navy); }
  .traits li::after {
    content: ""; position: absolute; left: 4px; top: 5px;
    width: 4px; height: 7px; border: solid var(--white);
    border-width: 0 1.5px 1.5px 0; transform: rotate(40deg);
  }

  .footer-navy {
    position: absolute; left: 0; top: 1096px; width: 849px; height: 80px;
    background: var(--navy);
  }
  .footer-red {
    position: absolute; left: 208px; top: 1071px; width: 641px; height: 95px;
    background: var(--red);
  }
  .district-mark {
    position: absolute; left: 147px; top: 1074px; width: 80px; height: 80px;
    border-radius: 50%; background: var(--white); border: 4px solid var(--navy);
  }
  .district-name {
    position: absolute; left: 291px; top: 1086px;
    font-family: "Montserrat", sans-serif; font-weight: 500;
    color: var(--white); font-size: 29px; line-height: 1;
  }
  .district-motto {
    position: absolute; left: 291px; top: 1124px;
    font-family: "Montserrat", sans-serif; font-weight: 500;
    color: var(--white); font-size: 24px; line-height: 1;
  }
</style>
</head>
<body>
<main class="poster">
  <div class="navy-column"></div>

  <h1>
    <span class="title-part title-left">Profile of</span>
    <span class="title-part title-right">A Trailblazer</span>
  </h1>

  <section class="pillar pillar-left" style="top:178px">
    <h2>Communicator</h2>
    <ul class="traits">
      <li>Expresses ideas clearly and respectfully (written &amp; verbal).</li>
      <li>Listens actively and understands diverse perspectives.</li>
      <li>Adjusts communication to suit the audience and context.</li>
    </ul>
  </section>

  <section class="pillar pillar-left" style="top:449px">
    <h2>Critical Thinker</h2>
    <ul class="traits">
      <li>Questions, analyzes, and evaluates information from multiple sources.</li>
      <li>Identifies and solves complex problems creatively.</li>
      <li>Uses evidence and diverse perspectives to form reasoned conclusions and make informed decisions.</li>
    </ul>
  </section>

  <section class="pillar pillar-left" style="top:725px">
    <h2>Responsible</h2>
    <ul class="traits">
      <li>Takes ownership of actions, choices, and commitments now and in future aspirations.</li>
      <li>Takes pride in managing time, resources, and self while striving to meet high expectations.</li>
      <li>Acts with integrity while advocating for themselves and others.</li>
    </ul>
  </section>

  <section class="pillar pillar-right" style="top:178px">
    <h2>Adaptable</h2>
    <ul class="traits">
      <li>Responds productively to new situations, challenges, and constructive feedback.</li>
      <li>Learns from new experiences and applies prior knowledge in an ever-changing world.</li>
      <li>Adjusts behavior and approach to engage effectively with diverse groups and environments.</li>
    </ul>
  </section>

  <section class="pillar pillar-right" style="top:463px">
    <h2>Collaborator</h2>
    <ul class="traits">
      <li>Demonstrates strong teamwork by contributing effectively and cooperatively toward shared goals.</li>
      <li>Listens actively and values diverse ideas and perspectives.</li>
      <li>Engages respectfully, knowing when to compromise, support, or take the lead.</li>
    </ul>
  </section>

  <section class="pillar pillar-right" style="top:737px">
    <h2>Compassionate</h2>
    <ul class="traits">
      <li>Understands and acknowledges others' feelings, perspectives, and experiences.</li>
      <li>Responds with kindness, patience, empathy, and support.</li>
      <li>Seeks to connect with others and contribute positively to their well-being and the community's well-being.</li>
    </ul>
  </section>

  <footer>
    <div class="footer-navy"></div>
    <div class="footer-red"></div>
    <div class="district-mark" aria-hidden="true"></div>
    <p class="district-name">Harlow Creek Public Schools</p>
    <p class="district-motto">Excellence in Academics, Arts &amp; Athletics</p>
  </footer>
</main>
</body>
</html>
```